We need a business card for our gym. We are a PowerCore affiliate in Decatur Georgie established 2008. Our company name is Rally Functional Fitness. PowerCore Building Prime Fitness. Instagram and website is @rallygym. Hashtags we use #rallywithheart #madetorally We want something similar to the the black and neon green design attached but a different color scheme. No neon colors. Are company colors are the same as the blue and white card attached. We are open to ideas as far as colors however - just no neon.

Contact Information for Business Card

Rally Functional Fitness
472 Halvern Drive
Decatur GA 30041
Phone 404.555.0187 Website www.rallygym.example

Font styles to use
Other font styles liked:
• Futura Extra Bold Condensed

Colors

Designer to choose colors to be used in the design.

Requirements
Must have
• Our primary font we typically use for our name is Futura Extra Bold Condensed
Nice to have
• I attached a card from that is black and neon green from Zorva that we would like something similar. The blue and white is more similar to our colors. We also use have used black and white in the past. We use the chevrons as out logo. We are a PowerCore affiliate so I included a logo from them as well that may or may not be used on the card. Our instagram is @rallygym hashtags #madetorally #rallywithheart
Should not have
• No neon colors

```html
<!DOCTYPE html>
<html lang="en">
<head>
<meta charset="utf-8">
<title>Rally Functional Fitness – Business Card</title>
<link rel="stylesheet" href="https://fonts.googleapis.com/css2?family=Anton&family=Montserrat:wght@300;400&display=swap">
<style>
  :root {
    --canvas-bg: #d2d2d2;
    --brand-blue: #135c9a;
    --brand-blue-light: #1a7fc3;
    --card-white: #ffffff;
    --text-blue: #1565a8;
  }
  * { margin: 0; padding: 0; box-sizing: border-box; }
  html, body {
    width: 1200px; height: 800px; overflow: hidden;
    background: var(--canvas-bg);
  }
  .canvas {
    position: relative; width: 1200px; height: 800px;
    display: flex; align-items: center; justify-content: center; gap: 40px;
  }
  .card {
    position: relative; width: 520px; height: 297px; overflow: hidden;
    box-shadow: 0 2px 6px rgba(0,0,0,0.25);
  }

  /* Front */
  .card--front {
    background: linear-gradient(100deg, var(--brand-blue) 0%, var(--brand-blue-light) 35%, var(--brand-blue) 65%, var(--brand-blue) 100%);
    display: flex; align-items: center; justify-content: center; gap: 14px;
  }
  .front-mark {
    width: 22px; height: 22px; background: var(--card-white);
  }
  .front-name {
    font-family: "Anton", sans-serif; font-weight: 400;
    font-size: 56px; letter-spacing: 2px; color: var(--card-white);
    line-height: 1;
  }

  /* Back */
  .card--back { background: var(--card-white); }
  .back-band {
    position: absolute; top: 0; right: 0; width: 170px; height: 100%;
    background: var(--brand-blue);
  }
  .back-band--thin {
    right: 190px; width: 26px;
  }
  .back-info {
    position: absolute; left: 34px; top: 28px;
    color: var(--text-blue);
  }
  .wordmark {
    font-family: "Anton", sans-serif; font-weight: 400; color: var(--text-blue);
    text-transform: uppercase; line-height: 1;
  }
  .wordmark__name { font-size: 56px; letter-spacing: 1px; }
  .wordmark__tag { font-size: 17px; letter-spacing: 1px; margin-top: 4px; }
  .person { margin-top: 14px; }
  .person__name {
    font-family: "Anton", sans-serif; font-size: 17px; letter-spacing: 1.5px;
    color: var(--text-blue); text-transform: uppercase;
  }
  .person__title {
    font-family: "Montserrat", sans-serif; font-weight: 300;
    font-size: 13px; letter-spacing: 1px; text-transform: uppercase;
  }
  .divider {
    width: 34px; height: 1px; background: var(--text-blue); margin: 10px 0 9px;
  }
  .contact {
    font-family: "Montserrat", sans-serif; font-weight: 400;
    font-size: 12px; line-height: 1.45; color: var(--text-blue);
  }
  .contact__row { display: flex; align-items: center; gap: 6px; }
  .contact__row svg { width: 10px; height: 10px; fill: var(--text-blue); }
  .contact__address { margin-bottom: 3px; }
</style>
</head>
<body>
<main class="canvas">
  <section class="card card--front" aria-label="Card front">
    <span class="front-mark"></span>
    <span class="front-name">RALLY</span>
  </section>

  <section class="card card--back" aria-label="Card back">
    <div class="back-band back-band--thin"></div>
    <div class="back-band"></div>
    <div class="back-info">
      <div class="wordmark">
        <div class="wordmark__name">RALLY</div>
        <div class="wordmark__tag">Functional Fitness</div>
      </div>
      <div class="person">
        <div class="person__name">Nathan&nbsp;&nbsp;Welker</div>
        <div class="person__title">Expert Coaches</div>
      </div>
      <div class="divider"></div>
      <div class="contact">
        <div class="contact__address">472 Halvern Drive<br>Decatur GA 30041</div>
        <div class="contact__row">
          <svg viewBox="0 0 24 24" aria-hidden="true"><path d="M6.6 10.8a15.1 15.1 0 0 0 6.6 6.6l2.2-2.2a1 1 0 0 1 1-.25 11.4 11.4 0 0 0 3.6.57 1 1 0 0 1 1 1V20a1 1 0 0 1-1 1A17 17 0 0 1 3 4a1 1 0 0 1 1-1h3.5a1 1 0 0 1 1 1c0 1.25.2 2.45.57 3.57a1 1 0 0 1-.25 1z"/></svg>
          <span>404.555.0187</span>
        </div>
        <div class="contact__row">
          <svg viewBox="0 0 24 24" aria-hidden="true"><path d="M12 2a10 10 0 1 0 0 20 10 10 0 0 0 0-20zm6.9 9h-3a15 15 0 0 0-1.4-6 8 8 0 0 1 4.4 6zM12 4.1c.9 1.3 1.7 3.6 1.9 6.9h-3.8c.2-3.3 1-5.6 1.9-6.9zM9.5 5a15 15 0 0 0-1.4 6h-3a8 8 0 0 1 4.4-6zM5.1 13h3a15 15 0 0 0 1.4 6 8 8 0 0 1-4.4-6zm6.9 6.9c-.9-1.3-1.7-3.6-1.9-6.9h3.8c-.2 3.3-1 5.6-1.9 6.9zm2.5-.9a15 15 0 0 0 1.4-6h3a8 8 0 0 1-4.4 6z"/></svg>
          <span>www.rallygym.example</span>
        </div>
      </div>
    </div>
  </section>
</main>
</body>
</html>
```